Stylish new business card needed!

Hello everyone! I am in need of a new business card design for an alarm company here in Hurricane WV. I have all fonts, color codes and logos provided for you use! We are a young company and like the style of a clean sleek looking business card. Would like it double sided, one side holding the logo and the other with your design!
Target Market(s)
The people that are looking for the newest tech for home automation and security
Industry/Entity Type
Alarm services; Home automation
Contact Information for Business Card
Name of person; position (Sales; Installer); Phone Number (555.418.7260); Employee cell Number; Website (www.GuardedByVelk.example); Employee Email; Double sided
Look and feel
Each slider illustrates characteristics of the customer's brand and the style your logo design should communicate.

```html
<!DOCTYPE html>
<html lang="en">
<head>
<meta charset="utf-8">
<title>Guarded By Velk — Business Card</title>
<link rel="stylesheet" href="https://fonts.googleapis.com/css2?family=Archivo:wght@800&family=Lato:wght@400;700&display=swap">
<style>
  :root {
    --backdrop: #2b2b2b;
    --card: #1e1f1f;
    --emboss: #353636;
    --orange: #f68c3e;
    --grey: #9a9a9a;
    --white: #f2f2f2;
  }
  * { margin: 0; padding: 0; box-sizing: border-box; }
  html, body { width: 1200px; height: 937px; overflow: hidden; }
  body {
    background: var(--backdrop);
    position: relative;
    font-family: "Lato", sans-serif;
  }
  .card {
    position: absolute;
    left: 250px;
    width: 700px;
    height: 400px;
    background: var(--card);
    overflow: hidden;
  }
  .card--front { top: 48px; }
  .card--back { top: 489px; }

  .brand-name {
    font-family: "Archivo", sans-serif;
    font-weight: 800;
    text-transform: uppercase;
    letter-spacing: 1px;
    line-height: 1;
  }
  .brand-tagline {
    font-family: "Archivo", sans-serif;
    font-weight: 800;
    text-transform: uppercase;
    font-size: 11px;
    letter-spacing: 1.2px;
  }

  /* Front: tone-on-tone brand name */
  .front-brand {
    position: absolute;
    left: 0; right: 0; top: 150px;
    text-align: center;
    color: var(--emboss);
  }
  .front-brand .brand-name { font-size: 52px; }
  .front-brand .brand-tagline { margin-top: 14px; font-size: 13px; }

  /* Back */
  .back-brand {
    position: absolute;
    left: 60px; top: 160px;
    width: 300px;
  }
  .back-brand .brand-name { font-size: 38px; color: var(--orange); }
  .back-brand .brand-tagline { margin-top: 12px; color: var(--orange); font-size: 10px; }

  .holder {
    position: absolute;
    left: 390px; top: 86px;
    width: 310px;
  }
  .holder__name {
    font-family: "Archivo", sans-serif;
    font-weight: 800;
    font-size: 27px;
    color: var(--orange);
    text-transform: uppercase;
    letter-spacing: 0.5px;
  }
  .holder__role {
    font-size: 15px;
    color: var(--white);
    margin-top: 2px;
  }
  .holder__rule {
    height: 2px;
    background: var(--orange);
    margin: 12px 0 16px;
  }
  .contact-list { list-style: none; }
  .contact-list li {
    display: flex;
    align-items: center;
    gap: 10px;
    color: var(--white);
    font-size: 16px;
    line-height: 1;
    margin-bottom: 10px;
  }
  .contact-list svg { width: 14px; height: 14px; flex: none; }
</style>
</head>
<body>

  <section class="card card--front" aria-label="Card front">
    <div class="front-brand">
      <div class="brand-name">Guarded By Velk</div>
      <div class="brand-tagline">Automation and Security Services</div>
    </div>
  </section>

  <section class="card card--back" aria-label="Card back">
    <div class="back-brand">
      <div class="brand-name">Guarded<br>By Velk</div>
      <div class="brand-tagline">Automation and Security Services</div>
    </div>

    <div class="holder">
      <div class="holder__name">Dale Corwin</div>
      <div class="holder__role">Manager</div>
      <div class="holder__rule"></div>
      <ul class="contact-list">
        <li>
          <svg viewBox="0 0 14 14" aria-hidden="true"><rect x="3.5" y="0.8" width="7" height="12.4" rx="1.2" fill="none" stroke="var(--orange)" stroke-width="1.5"/><circle cx="7" cy="11" r="0.8" fill="var(--orange)"/></svg>
          000-000-0000
        </li>
        <li>
          <svg viewBox="0 0 14 14" aria-hidden="true"><path d="M3 1.5 L5.2 1.5 L6 4.5 L4.5 5.6 Q5.8 8.4 8.4 9.5 L9.5 8 L12.5 8.8 L12.5 11 Q12.3 12.5 10.8 12.5 Q2 11.6 1.5 3 Q1.5 1.5 3 1.5 Z" fill="var(--orange)"/></svg>
          555.418.7260
        </li>
        <li>
          <svg viewBox="0 0 14 14" aria-hidden="true"><rect x="1" y="3" width="12" height="8.5" fill="var(--orange)"/><path d="M1 3 L7 8 L13 3" fill="none" stroke="var(--card)" stroke-width="1.2"/></svg>
          mail@GuardedByVelk.example
        </li>
        <li>
          <svg viewBox="0 0 14 14" aria-hidden="true"><circle cx="7" cy="7" r="6" fill="var(--orange)"/><path d="M1 7 H13 M7 1 Q3.5 7 7 13 M7 1 Q10.5 7 7 13" fill="none" stroke="var(--card)" stroke-width="1"/></svg>
          www.GuardedByVelk.example
        </li>
      </ul>
    </div>
  </section>

</body>
</html>
```